The Plate Compass

Cutting Through the Noise to What Actually Works.

Nutrition book

Target Market(s)

People looking to be or get healthy and eat right.

```html
<!DOCTYPE html>
<html lang="en">
<head>
<meta charset="UTF-8">
<title>The Plate Compass — Book Cover</title>
<link href="https://fonts.googleapis.com/css2?family=Barlow:wght@300;400;700;800&display=swap" rel="stylesheet">
<style>
  :root {
    --backdrop: #222222;
    --cover-blue: #2f4fb2;
    --cover-blue-deep: #2644a3;
    --title-cream: #f3eee2;
    --tape-paper: #ece6d9;
    --tape-edge: #d8d0bf;
    --label-navy: #1f2b47;
    --photo-light: #e9e4d6;
    --photo-mid: #b79a68;
    --photo-edge: #d9d6cc;
  }
  * { margin: 0; padding: 0; box-sizing: border-box; }
  html, body {
    width: 1200px; height: 1200px; overflow: hidden;
    background: var(--backdrop);
  }
  .cover {
    position: absolute;
    left: 200px; top: 35px;
    width: 800px; height: 1130px;
    background: linear-gradient(160deg, var(--cover-blue) 0%, var(--cover-blue-deep) 100%);
    font-family: 'Barlow', sans-serif;
    overflow: hidden;
  }
  .title {
    position: absolute;
    left: 100px; top: 110px;
    color: var(--title-cream);
    font-weight: 800;
    text-transform: uppercase;
    line-height: 0.95;
  }
  .title-kicker { display: block; font-size: 30px; letter-spacing: 1px; margin-bottom: 6px; }
  .title-main { display: block; font-size: 66px; letter-spacing: 0.5px; }
  .plate-photo {
    position: absolute;
    left: 165px; top: 305px;
    width: 510px; height: 510px;
    border-radius: 50%;
    background: radial-gradient(circle at 50% 50%, var(--photo-mid) 0%, var(--photo-light) 60%, var(--photo-edge) 100%);
    box-shadow: 0 18px 30px rgba(10, 20, 60, 0.35);
  }
  .tape {
    position: absolute;
    height: 72px;
    display: flex; align-items: center; justify-content: center;
    background: var(--tape-paper);
    border-left: 4px solid var(--tape-edge);
    border-right: 4px solid var(--tape-edge);
    box-shadow: 0 6px 12px rgba(10, 20, 60, 0.35);
    color: var(--label-navy);
    font-weight: 700;
    font-size: 26px;
    letter-spacing: 1px;
    text-transform: uppercase;
    white-space: nowrap;
  }
  .tape-calories  { left: 70px;  top: 385px; width: 250px; transform: rotate(-16deg); }
  .tape-protein   { left: 360px; top: 350px; width: 300px; transform: rotate(3deg); }
  .tape-noise     { left: 555px; top: 470px; width: 140px; height: 64px; font-size: 22px; transform: rotate(-36deg); }
  .tape-quality   { left: 90px;  top: 525px; width: 260px; font-size: 22px; transform: rotate(6deg); }
  .tape-supps     { left: 475px; top: 610px; width: 250px; font-size: 22px; transform: rotate(-26deg); }
  .tape-timing    { left: 200px; top: 755px; width: 330px; font-size: 24px; transform: rotate(-4deg); }
  .tagline {
    position: absolute;
    left: 0; top: 905px;
    width: 800px;
    padding-left: 260px;
    color: var(--title-cream);
    font-size: 26px;
    line-height: 1.35;
    text-align: center;
  }
  .tagline-lead { display: block; font-weight: 300; }
  .tagline-strong { display: block; font-weight: 700; }
</style>
</head>
<body>
  <main class="cover">
    <h1 class="title">
      <span class="title-kicker">The</span>
      <span class="title-main">Plate</span>
      <span class="title-main">Compass</span>
    </h1>

    <div class="plate-photo" role="img" aria-label="Photo of a white plate with seared salmon, lemon slices, broccolini and herbed roast potatoes"></div>

    <div class="tape tape-calories">Calories</div>
    <div class="tape tape-protein">Protein</div>
    <div class="tape tape-noise">Noise</div>
    <div class="tape tape-quality">Food Quality</div>
    <div class="tape tape-supps">Supplements</div>
    <div class="tape tape-timing">Meal Timing</div>

    <p class="tagline">
      <span class="tagline-lead">Cutting Through the Noise</span>
      <span class="tagline-strong">to What Actually Works.</span>
    </p>
  </main>
</body>
</html>
```